SkyvornQ Business Cards and Stationary Design

Need a design for our business cards and stationary. I want to carry on the theme of the logo. I want the business cards to have a design on the back. I would like the business cards and the stationary to carry the same theme, design scheme, and branding

Target Market(s)

Airlines and Maintenance Facilities

Industry/Entity Type

Aviation

Contact Information for Business Card

Name
Position Title
Address: 4827 Trellis Hollow Road, Halden Bay, Corvane, 34951
Office Number
Mobile Number
Email
Website

Font styles to use
Serif
Sans Serif

Colors

Designer to choose colors to be used in the design.

```html
<!DOCTYPE html>
<html lang="en">
<head>
<meta charset="utf-8">
<title>SkyvornQ Business Card</title>
<link href="https://fonts.googleapis.com/css2?family=Montserrat:wght@300;400;700;800&display=swap" rel="stylesheet">
<style>
  :root {
    --bg: #ebebeb;
    --paper: #f7f7f7;
    --ink: #2b2f3a;
    --ink-soft: #55596a;
    --rule: #9a9ca3;
    --brand-navy: #22304f;
    --brand-blue: #2f86b3;
    --icon-blue: #3a93d0;
    --white: #ffffff;
  }
  * { box-sizing: border-box; margin: 0; padding: 0; }
  html, body {
    width: 1200px; height: 1149px; overflow: hidden;
    background: var(--bg);
    font-family: "Montserrat", sans-serif;
  }
  .sheet {
    position: relative; width: 1200px; height: 1149px;
    display: flex; flex-direction: column; align-items: center; justify-content: center;
    gap: 70px;
  }
  .card {
    position: relative; width: 700px; height: 400px;
    box-shadow: 0 10px 30px rgba(0,0,0,0.12);
    overflow: hidden;
  }
  /* Front */
  .card--front { background: var(--paper); color: var(--ink); }
  .holder { position: absolute; left: 48px; top: 44px; }
  .holder__name { font-weight: 800; font-size: 25px; letter-spacing: 0.5px; color: var(--ink); }
  .holder__title { font-weight: 300; font-size: 15px; color: var(--ink-soft); margin-top: 2px; }
  .holder__rule { width: 250px; height: 1px; background: var(--rule); margin: 14px 0 12px; }
  .contact { list-style: none; }
  .contact li {
    display: flex; align-items: center; gap: 10px;
    font-weight: 400; font-size: 15px; color: var(--ink-soft); line-height: 24px;
  }
  .contact svg { width: 14px; height: 14px; flex: none; }
  .divider { position: absolute; left: 48px; right: 48px; top: 262px; height: 1px; background: var(--rule); }
  .brand {
    position: absolute; display: flex; align-items: center; gap: 14px;
  }
  .brand__name { font-weight: 800; letter-spacing: 7px; }
  .brand__mark { border-radius: 50%; }
  .card--front .brand { right: 48px; top: 160px; }
  .card--front .brand__name { font-size: 30px; color: var(--brand-navy); }
  .card--front .brand__mark { width: 44px; height: 44px; border: 5px solid var(--brand-blue); }
  .address {
    position: absolute; right: 48px; bottom: 44px; text-align: right;
    font-weight: 400; font-size: 15px; line-height: 23px; color: var(--ink-soft);
  }
  /* Back */
  .card--back {
    background: linear-gradient(200deg, var(--brand-blue) 0%, #2b5c86 45%, var(--brand-navy) 100%);
    color: var(--white);
  }
  .card--back .brand { left: 50%; top: 150px; transform: translateX(-50%); }
  .card--back .brand__name { font-size: 36px; color: var(--white); }
  .card--back .brand__mark { width: 54px; height: 54px; border: 6px solid var(--white); }
  .web {
    position: absolute; left: 0; right: 0; top: 228px; text-align: center;
    font-weight: 400; font-size: 16px; letter-spacing: 2px; color: var(--white);
  }
</style>
</head>
<body>
<main class="sheet">
  <section class="card card--front">
    <div class="holder">
      <h1 class="holder__name">Daniel REEVES</h1>
      <p class="holder__title">CEO / Founder</p>
      <div class="holder__rule"></div>
      <ul class="contact">
        <li><svg viewBox="0 0 14 14"><path d="M3 1 L5.5 1 L6.5 4 L5 5.2 Q6.3 8 8.8 9 L10 7.5 L13 8.5 L13 11 Q12 13 10 13 Q3 12 1 4 Q1 2 3 1 Z" fill="var(--icon-blue)"/></svg>000.000.0000</li>
        <li><svg viewBox="0 0 14 14"><rect x="3.5" y="1" width="7" height="12" rx="1.3" fill="none" stroke="var(--icon-blue)" stroke-width="1.4"/></svg>000.000.0000</li>
        <li><svg viewBox="0 0 14 14"><rect x="1" y="3" width="12" height="8.5" fill="none" stroke="var(--icon-blue)" stroke-width="1.3"/><path d="M1 3 L7 8 L13 3" fill="none" stroke="var(--icon-blue)" stroke-width="1.3"/></svg>daniel@skyvornq.com</li>
        <li><svg viewBox="0 0 14 14"><g fill="none" stroke="var(--icon-blue)" stroke-width="1.1"><circle cx="7" cy="7" r="6"/><ellipse cx="7" cy="7" rx="2.6" ry="6"/><path d="M1 7 H13 M2 4 H12 M2 10 H12"/></g></svg>www.skyvornq.com</li>
      </ul>
    </div>
    <div class="brand">
      <span class="brand__name">SKYVORNQ</span>
      <span class="brand__mark"></span>
    </div>
    <div class="divider"></div>
    <p class="address">4827 Trellis Hollow Road<br>Halden Bay, Corvane, 34951</p>
  </section>

  <section class="card card--back">
    <div class="brand">
      <span class="brand__name">SKYVORNQ</span>
      <span class="brand__mark"></span>
    </div>
    <p class="web">www.skyvornq.com</p>
  </section>
</main>
</body>
</html>
```